Lmworks Business Card Design

I need a business card design for a new Business, that is focused on Custom Made Designer Furniture. that is aimed at the mid to high end markets. I would like a card that would in some way portray what I do for my clients in the way we are able to make any idea a reality and also work within a set budget to meet their requirements.
I like quite contemporary colours and styling and I want the final design to communicate a Contemporary and Professional image.

Target Market(s)

mid to high end market

Industry/Entity Type

Business

Contact Information for Business Card

Lmworks
Gareth Lindqvist
18 Wendover Ave, Auckland, New Zealand 0627.

Requirements
Nice to have
• I would also like to utilize the spot gloss or raised print on my cards

```html
<!DOCTYPE html>
<html lang="en">
<head>
<meta charset="utf-8">
<title>Lmworks Business Card</title>
<link href="https://fonts.googleapis.com/css2?family=Poiret+One&family=Open+Sans:wght@600&display=swap" rel="stylesheet">
<style>
  :root {
    --page: #ffffff;
    --card: #000000;
    --ink: #ffffff;
    --stripe: #5a5a5a;
    --stripe-gap: #262626;
    --ornament-light: #cfcfcf;
    --ornament-mid: #5e5e5e;
    --ornament-dark: #111111;
  }
  * { margin: 0; padding: 0; box-sizing: border-box; }
  html, body {
    width: 1200px;
    height: 741px;
    overflow: hidden;
    background: var(--page);
  }
  .card {
    position: absolute;
    left: 16px;
    top: 33px;
    width: 1168px;
    height: 678px;
    background: var(--card);
    color: var(--ink);
    overflow: hidden;
  }
  .ornament {
    position: absolute;
    left: 76px;
    top: 10px;
    width: 411px;
    height: 663px;
  }
  .stripe-band {
    position: absolute;
    left: 487px;
    top: 0;
    width: 86px;
    height: 100%;
    background: repeating-linear-gradient(
      to bottom,
      var(--stripe) 0 14px,
      var(--stripe-gap) 14px 23px
    );
  }
  .brand {
    position: absolute;
    left: 669px;
    top: 140px;
    width: 400px;
    text-align: center;
    font-family: "Poiret One", sans-serif;
    font-size: 78px;
    line-height: 1;
    letter-spacing: 1px;
  }
  .person {
    position: absolute;
    left: 683px;
    top: 282px;
    width: 400px;
    text-align: center;
  }
  .person-name {
    font-family: "Poiret One", sans-serif;
    font-variant: small-caps;
    font-size: 44px;
    line-height: 1;
    letter-spacing: 0.5px;
  }
  .person-role {
    font-family: "Open Sans", sans-serif;
    font-weight: 600;
    font-size: 18px;
    line-height: 1;
    margin-top: 8px;
  }
  .tagline {
    position: absolute;
    left: 583px;
    top: 400px;
    width: 600px;
    text-align: center;
    font-family: "Poiret One", sans-serif;
    font-variant: small-caps;
    font-size: 26px;
    letter-spacing: 0.5px;
  }
  .address {
    position: absolute;
    right: 44px;
    top: 536px;
    text-align: right;
    font-family: "Poiret One", sans-serif;
    font-variant: small-caps;
    font-size: 29px;
    line-height: 29px;
    font-style: normal;
  }
</style>
</head>
<body>
  <main class="card">
    <svg class="ornament" viewBox="0 0 411 663" role="img" aria-label="Swirling floral scroll ornament in silver and grey leaves">
      <defs>
        <radialGradient id="ornament-fill" cx="70%" cy="50%" r="65%">
          <stop offset="0%" stop-color="var(--ornament-light)"/>
          <stop offset="45%" stop-color="var(--ornament-mid)"/>
          <stop offset="100%" stop-color="var(--ornament-dark)"/>
        </radialGradient>
      </defs>
      <rect width="411" height="663" fill="url(#ornament-fill)"/>
    </svg>

    <div class="stripe-band"></div>

    <h1 class="brand">Lmworks</h1>

    <div class="person">
      <p class="person-name">Gareth Lindqvist</p>
      <p class="person-role">designer</p>
    </div>

    <p class="tagline">Custom Made Designer Furniture</p>

    <address class="address">
      18 Wendover Ave<br>
      Auckland<br>
      New Zealand 0627
    </address>
  </main>
</body>
</html>
```